Business card for event manager / organizer "waiter service"

Draft of a new valuable business card for my company.
Events, personnel service providers, festivals

```html
<!DOCTYPE html>
<html lang="de">
<head>
<meta charset="utf-8">
<title>Jonas Servierdienst – Visitenkarte</title>
<link rel="stylesheet" href="https://fonts.googleapis.com/css2?family=Montserrat:wght@600&family=Poppins:wght@300;400;600&display=swap">
<style>
  :root {
    --page-bg: #e9e6e2;
    --card-dark: #1b1a19;
    --card-mid: #2e2c2a;
    --accent: #c9692c;
    --text-light: #d8d3cd;
    --text-muted: #b9b2aa;
    --white: #f4f1ed;
  }
  * { margin: 0; padding: 0; box-sizing: border-box; }
  html, body {
    width: 1200px; height: 1047px; overflow: hidden;
    background: var(--page-bg);
  }
  .business-card {
    position: absolute;
    left: 100px; top: 250px;
    width: 1000px; height: 548px;
    border-radius: 22px;
    overflow: hidden;
    background: radial-gradient(ellipse at 65% 40%, var(--card-mid) 0%, var(--card-dark) 70%);
    box-shadow: 0 12px 40px rgba(0,0,0,0.25);
    font-family: "Poppins", sans-serif;
  }
  .brand {
    position: absolute; left: 40px; top: 42px;
    display: flex; align-items: center; gap: 14px;
  }
  .brand-mark {
    width: 74px; height: 74px; background: var(--accent);
  }
  .brand-text { display: flex; flex-direction: column; }
  .brand-name {
    font-family: "Poppins", sans-serif; font-weight: 600;
    font-size: 25px; line-height: 1.1; color: var(--white);
    letter-spacing: 0.5px;
  }
  .brand-slogan {
    margin-top: 6px;
    font-size: 10px; font-weight: 300; color: var(--text-muted);
    font-style: italic;
  }
  .owner-name {
    position: absolute; left: 40px; top: 184px;
    font-family: "Montserrat", sans-serif; font-weight: 600;
    font-size: 35px; color: var(--accent);
  }
  .owner-role {
    position: absolute; left: 42px; top: 237px;
    font-size: 22px; font-weight: 300; color: var(--text-light);
  }
  .contact-list {
    position: absolute; left: 40px; top: 293px;
    list-style: none;
  }
  .contact-item {
    display: flex; align-items: center; gap: 10px;
    height: 36.5px;
    font-size: 23px; font-weight: 300; color: var(--text-light);
    white-space: nowrap;
  }
  .contact-icon { width: 20px; height: 20px; flex: none; fill: var(--accent); }
  .social-square { width: 17px; height: 17px; background: var(--accent); border-radius: 3px; margin: 0 1.5px; flex: none; }
  .owner-photo {
    position: absolute; right: 30px; top: 36px;
    width: 400px; height: 512px;
    background: radial-gradient(ellipse at 50% 45%, #1f2a30 0%, #141a1d 45%, rgba(27,26,25,0) 72%);
  }
</style>
</head>
<body>
  <div class="business-card">
    <div class="brand">
      <div class="brand-mark"></div>
      <div class="brand-text">
        <span class="brand-name">JONAS<br>SERVIERDIENST</span>
        <span class="brand-slogan">...weil jedes Fest guten Service verdient!</span>
      </div>
    </div>

    <h1 class="owner-name">Jonas Brekenfeld</h1>
    <p class="owner-role">Inhaber</p>

    <ul class="contact-list">
      <li class="contact-item">
        <svg class="contact-icon" viewBox="0 0 24 24"><path d="M3 8c0-2 2-4 9-4s9 2 9 4v2h-5V8H8v2H3zM6 12h12l2 8H4z"/></svg>
        02361 208 47 13
      </li>
      <li class="contact-item">
        <svg class="contact-icon" viewBox="0 0 24 24"><path d="M3 8c0-2 2-4 9-4s9 2 9 4v2h-5V8H8v2H3zM6 12h12l2 8H4z"/></svg>
        0176 482 31 09
      </li>
      <li class="contact-item">
        <svg class="contact-icon" viewBox="0 0 24 24"><circle cx="12" cy="12" r="9"/><path d="M7 8c2 1 3 0 4 2s-1 3 1 5 2 3 1 5M15 5c-1 2 1 3 3 3" stroke="#1b1a19" stroke-width="1.8" fill="none"/></svg>
        www.jonas-servierdienst.de
      </li>
      <li class="contact-item">
        <svg class="contact-icon" viewBox="0 0 24 24"><path d="M3 6h18v12H3z"/><path d="M3 6l9 7 9-7" stroke="#1b1a19" stroke-width="1.6" fill="none"/></svg>
        info@jonas-servierdienst.de
      </li>
      <li class="contact-item">
        <svg class="contact-icon" viewBox="0 0 24 24"><path d="M12 2a7 7 0 0 0-7 7c0 5 7 13 7 13s7-8 7-13a7 7 0 0 0-7-7zm0 10a3 3 0 1 1 0-6 3 3 0 0 1 0 6z"/></svg>
        Birkenweg 5, 45701 Herten
      </li>
      <li class="contact-item">
        <span class="social-square"></span>
        www.social.de/jonasservierdienst
      </li>
    </ul>

    <div class="owner-photo" role="img" aria-label="Portraitfoto des Inhabers in dunklem Hemd, Hände in den Hüften"></div>
  </div>
</body>
</html>
```